Lanternfield Drinks business cards

We need a business card design for our new logo. The company is modern, progressive, professional, yet approachable. The key products are ready to drink bottles and cans of coffee based beverages.
These cards will be a critical part of the first impression made by our sales organization, business development team, and all external facing personnel.
Card can be a vertical or horizontal orientation.

Target Market(s)

Customers, suppliers, business partners

Industry/Entity Type

Business

Contact Information for Business Card

Business cards should feature Company Name and Logo.

Font styles to use
Serif

Colors

Designer to choose colors to be used in the design.

Requirements
Must have
• Strong readability of Name, phone #, mobile number and email address.
• Job title, website url, Street Address, and other details can be secondary level readability.
Nice to have
• High impact, simplistic quality design.
• Ok to utilize the 'H in the box' separate from the company name

```html
<!DOCTYPE html>
<html lang="en">
<head>
<meta charset="utf-8">
<title>Lanternfield Drinks – Business Cards</title>
<link href="https://fonts.googleapis.com/css2?family=Cinzel:wght@700&family=Lato:wght@400;700&display=swap" rel="stylesheet">
<style>
  :root {
    --bg: #141414;
    --ink-dark: #261d1f;
    --orange: #e8703f;
    --orange-light: #f0955a;
    --gold: #f5b335;
    --white: #ffffff;
    --paper: #f4f4f4;
    --cream: #fff3e8;
  }
  * { margin: 0; padding: 0; box-sizing: border-box; }
  html, body { width: 1200px; height: 864px; overflow: hidden; background: var(--bg); }
  .canvas { position: relative; width: 1200px; height: 864px; }

  .card {
    position: absolute; width: 500px; height: 286px; overflow: hidden;
    box-shadow: 0 14px 30px rgba(0,0,0,.55);
  }
  .card-front { left: 70px; top: 290px; }
  .card-back  { left: 630px; top: 290px; }
  .card-art { position: absolute; inset: 0; }

  /* front */
  .brand-mark {
    position: absolute; left: 330px; top: 40px; width: 150px;
    display: flex; flex-direction: column; align-items: center; gap: 10px;
  }
  .brand-square { width: 34px; height: 34px; border: 3px solid var(--orange); }
  .brand-name {
    font-family: "Cinzel", serif; font-weight: 700; font-size: 15px;
    color: var(--orange); letter-spacing: 1px; text-align: center; line-height: 1.2;
  }
  .person { position: absolute; left: 318px; top: 145px; width: 170px; text-align: center; color: var(--white); }
  .person-name { font-family: "Cinzel", serif; font-weight: 700; font-size: 13px; letter-spacing: .5px; }
  .person-title { font-family: "Lato", sans-serif; font-size: 11px; margin-top: 1px; }

  .contact-list {
    position: absolute; left: 24px; top: 172px; list-style: none;
    font-family: "Lato", sans-serif; font-size: 11.5px; color: var(--cream);
  }
  .contact-list li { display: flex; align-items: center; gap: 9px; height: 17px; }
  .contact-list svg { width: 11px; height: 11px; flex: none; }
  .address {
    position: absolute; left: 318px; top: 218px;
    font-family: "Lato", sans-serif; font-size: 11.5px; line-height: 16px; color: var(--cream);
  }

  /* back */
  .product-visual { position: absolute; left: 0; top: 0; width: 500px; height: 78px; }
  .back-brand {
    position: absolute; left: 24px; top: 140px; display: flex; align-items: center; gap: 16px;
  }
  .back-square { width: 62px; height: 62px; border: 4px solid var(--white); }
  .back-name {
    font-family: "Cinzel", serif; font-weight: 700; font-size: 32px;
    color: var(--white); letter-spacing: 1px; line-height: 1;
  }
</style>
</head>
<body>
<main class="canvas">

  <section class="card card-front" aria-label="Business card front">
    <svg class="card-art" viewBox="0 0 500 286" aria-hidden="true">
      <defs>
        <linearGradient id="frontOrange" x1="0" y1="0" x2="0" y2="1">
          <stop offset="0" stop-color="#f0955a"/>
          <stop offset="1" stop-color="#e06a3a"/>
        </linearGradient>
        <linearGradient id="frontDark" x1="0" y1="0" x2="1" y2="1">
          <stop offset="0" stop-color="#2b2123"/>
          <stop offset="1" stop-color="#1f1719"/>
        </linearGradient>
      </defs>
      <rect width="500" height="286" fill="url(#frontOrange)"/>
      <rect width="500" height="138" fill="url(#frontDark)"/>
      <rect y="138" width="500" height="5" fill="#e8703f"/>
      <rect y="145" width="500" height="4" fill="#f5b335"/>
      <polygon points="300,138 500,138 500,180 330,180 318,168 300,148" fill="#241b1d"/>
    </svg>

    <div class="brand-mark">
      <span class="brand-square"></span>
      <span class="brand-name">Lanternfield Drinks</span>
    </div>

    <div class="person">
      <p class="person-name">DANIEL WHITCOMBE</p>
      <p class="person-title">Managing Director</p>
    </div>

    <ul class="contact-list">
      <li><svg viewBox="0 0 12 12"><rect x=".5" y=".5" width="11" height="11" rx="2" fill="none" stroke="#fff3e8"/><path d="M3.5 3c1 3 2.5 4.5 5 5.5" stroke="#fff3e8" stroke-width="1.5" fill="none"/></svg>425.555.0148</li>
      <li><svg viewBox="0 0 12 12"><rect x=".5" y=".5" width="11" height="11" rx="2" fill="none" stroke="#fff3e8"/><rect x="4" y="2.5" width="4" height="7" rx=".8" fill="none" stroke="#fff3e8"/></svg>206.555.0192</li>
      <li><svg viewBox="0 0 12 12"><rect x=".5" y=".5" width="11" height="11" rx="2" fill="none" stroke="#fff3e8"/><path d="M2.5 4h7v4.5h-7zM2.5 4l3.5 2.5L9.5 4" fill="none" stroke="#fff3e8"/></svg>dan@lanternfielddrinks.com</li>
      <li><svg viewBox="0 0 12 12"><rect x=".5" y=".5" width="11" height="11" rx="2" fill="none" stroke="#fff3e8"/><circle cx="6" cy="6" r="3.3" fill="none" stroke="#fff3e8"/><path d="M2.7 6h6.6M6 2.7v6.6" stroke="#fff3e8" stroke-width=".7"/></svg>www.lanternfielddrinks.com</li>
    </ul>

    <address class="address">410 Harbor Rd.<br>Westbrook, NY 11790</address>
  </section>

  <section class="card card-back" aria-label="Business card back">
    <svg class="card-art" viewBox="0 0 500 286" aria-hidden="true">
      <defs>
        <linearGradient id="backOrange" x1="0" y1="0" x2="1" y2="1">
          <stop offset="0" stop-color="#e8703f"/>
          <stop offset="1" stop-color="#f0955a"/>
        </linearGradient>
      </defs>
      <rect width="500" height="286" fill="url(#backOrange)"/>
      <rect width="500" height="78" fill="#f4f4f4"/>
      <rect y="80" width="500" height="5" fill="#f5b335"/>
      <rect y="85" width="500" height="4" fill="#ffffff"/>
      <rect y="104" width="500" height="4" fill="#f5b335"/>
    </svg>
    <div class="product-visual" role="img" aria-label="Faint line drawing of coffee beverage bottles and cans" style="background: linear-gradient(90deg, #f6f6f6, #ececec 60%, #f3f3f3);"></div>
    <div class="back-brand">
      <span class="back-square"></span>
      <span class="back-name">LANTERNFIELD DRINKS</span>
    </div>
  </section>

</main>
</body>
</html>
```